Up to the Challenge - PPT Template with Splash Slide

We are looking for a PPT template that has 4 slides.
1. Splash slide (Creative, fun, no content, a visual representation of the theme)
2. Section header slide
3. Content Slide
4. Content Slide, another design option
The theme is 'UP to the Challenge'. The design should reflect this theme.
The colors should be in Purple (#864B99), Blue (#0A80C2), and Green (#52B054).

```html
<!DOCTYPE html>
<html lang="en">
<head>
<meta charset="utf-8">
<title>Up to the Challenge – Slide Template</title>
<link rel="stylesheet" href="https://fonts.googleapis.com/css2?family=Roboto:wght@400;500;700;900&display=swap">
<style>
:root{
  --purple:#864B99;
  --blue:#0A80C2;
  --green:#52B054;
  --page:#EDEDED;
  --white:#FFFFFF;
  --ink:#1E1E1E;
  --body:#555555;
}
*{box-sizing:border-box;margin:0;padding:0}
html,body{width:1029px;height:1200px;overflow:hidden;background:var(--page);font-family:'Roboto',sans-serif}
.board{position:relative;width:1029px;height:1200px}
.slide{position:absolute;width:457px;height:258px;background:var(--white);overflow:hidden;box-shadow:0 1px 4px rgba(0,0,0,.08)}
.col-a{left:39px}.col-b{left:533px}
.row-1{top:41px}.row-2{top:328px}.row-3{top:614px}.row-4{top:901px}

.visual{position:absolute;inset:0}
.visual.maze{background:linear-gradient(180deg,#2b3d9e 0%,#2a2f8c 55%,#4d2f8e 80%,#70307f 100%)}
.visual.fishbowl{background:radial-gradient(ellipse at 45% 70%,#e8f0fa 0%,#b8ccec 35%,#7e9fd4 70%,#2d3e63 100%)}
.visual.faded{background:linear-gradient(160deg,#f7f7f8 0%,#efeff1 50%,#f3efea 100%)}
.visual.tinted{background:linear-gradient(160deg,#1489cc 0%,#0A80C2 50%,#0b73b0 100%)}

.title-band{position:absolute;left:0;top:15.6px;width:286px;height:30px;background:var(--blue);
  clip-path:polygon(0 0,100% 0,95.5% 100%,0 100%);
  color:var(--white);font-weight:900;font-size:14.5px;letter-spacing:.4px;line-height:30px;padding-left:23px;text-transform:uppercase}

.footer{position:absolute;left:0;bottom:0;width:100%;height:23px;background:var(--purple);color:var(--white);font-size:5.6px;line-height:23px;padding-left:23px}
.footer .page-no{position:absolute;left:351px;top:0;width:74px;height:23px;background:var(--blue);text-align:center;font-weight:500}
.footer.wide .page-no{left:351px}

.section-title{position:absolute;left:86px;top:98px;width:286px;height:62px;border-top:.6px solid rgba(255,255,255,.55);border-bottom:.6px solid rgba(255,255,255,.55);
  color:var(--white);font-weight:900;font-size:25px;letter-spacing:.6px;text-align:center;line-height:61px}

.bullets{position:absolute;list-style:none;font-size:6.6px;color:var(--body);line-height:17.1px}
.bullets li{position:relative;padding-left:17px}
.bullets li svg{position:absolute;left:0;top:5.2px;width:6.5px;height:6.5px}
.bullets.full{left:32px;top:64px;width:400px}
.bullets.half-a{left:36px;top:64px;width:190px;text-align:justify}
.bullets.half-b{left:243px;top:64px;width:190px}

.lead{position:absolute;left:23px;top:63px;width:188px;font-size:6.6px;line-height:17.1px;color:var(--body);text-align:justify}
.lead p+p{margin-top:17.1px}
.illustration{position:absolute;left:232px;top:64px;width:192px;height:152px;border-radius:17px;background:linear-gradient(160deg,#b3cdec 0%,#9fbfe6 100%)}

.feature{position:absolute;top:73px;width:110px}
.feature .badge{width:45px;height:45px;border-radius:50%;display:flex;align-items:center;justify-content:center}
.feature .badge svg{width:22px;height:22px}
.feature h3{margin-top:9px;font-size:9.5px;font-weight:500;color:var(--ink)}
.feature p{margin-top:6px;font-size:5.6px;line-height:11px;color:var(--body);text-align:justify;width:107px}
.f1{left:42px}.f2{left:176px}.f3{left:310px}
.purple{background:var(--purple)}.blue{background:var(--blue)}.green{background:var(--green)}
</style>
</head>
<body>
<svg width="0" height="0" style="position:absolute">
  <symbol id="arrow-dot" viewBox="0 0 10 10">
    <circle cx="5" cy="5" r="4.2" fill="none" stroke="#0A80C2" stroke-width="1.4"/>
    <circle cx="5" cy="5" r="3" fill="#0A80C2"/>
    <path d="M3.3 5h3.2M5 3.5 6.6 5 5 6.5" stroke="#fff" stroke-width="1" fill="none" stroke-linecap="round"/>
  </symbol>
</svg>

<main class="board">

  <section class="slide col-a row-1">
    <div class="visual maze" role="img" aria-label="Vast blue maze with a lone figure standing at its entrance"></div>
  </section>

  <section class="slide col-b row-1">
    <div class="visual fishbowl" role="img" aria-label="Goldfish leaping from a small bowl into a larger bowl"></div>
  </section>

  <section class="slide col-a row-2">
    <div class="visual faded" role="img" aria-label="Faint photo of a hand turning letter blocks from impossible to possible"></div>
    <h2 class="title-band">Section Title</h2>
    <footer class="footer">(C) Copyright 2024 | All Rights Reserved<span class="page-no">Page 02 Of 08</span></footer>
  </section>

  <section class="slide col-b row-2">
    <div class="visual tinted" role="img" aria-label="Blue tinted photo of a hand turning letter blocks from impossible to possible"></div>
    <h2 class="section-title">SECTION TITLE HERE</h2>
  </section>

  <section class="slide col-a row-3">
    <h2 class="title-band">Who We Are (About Us)</h2>
    <ul class="bullets full">
      <li><svg><use href="#arrow-dot"/></svg>I must explain to you how all this mistaken idea of denouncing pleasure and praising pain was born and I will give you a complete account of the system, and expound the actual teachings of the great explorer of the trutt</li>
      <li><svg><use href="#arrow-dot"/></svg>Master-builder of human happiness. No one rejects, dislikes, or avoids pleasure itself, because it is pleasure, but because those who do not know how to pursue pleasure rationally encounter consequences that are extremely painful.</li>
      <li><svg><use href="#arrow-dot"/></svg>Nor again is there anyone who loves or pursues or desires to obtain pain of itself, because it is pain</li>
      <li><svg><use href="#arrow-dot"/></svg>To take a trivial example, which of us ever undertakes laborious physical exercise, except to obtain some advantage from it?</li>
      <li><svg><use href="#arrow-dot"/></svg>But who has any right to find fault with a man who chooses to enjoy a pleasure that has no annoying consequences, or one who avoids a pain that produces no resultant pleasure</li>
      <li><svg><use href="#arrow-dot"/></svg>I must explain to you how all this mistaken idea of denouncing pleasure and praising pain</li>
    </ul>
    <footer class="footer">(C) Copyright 2024 | All Rights Reserved<span class="page-no">Page 03 Of 08</span></footer>
  </section>

  <section class="slide col-b row-3">
    <h2 class="title-band">Who We Are (About Us)</h2>
    <ul class="bullets half-a">
      <li><svg><use href="#arrow-dot"/></svg>I must explain to you how all this mistaken idea of denoun cing pleasure and praising pain was born an</li>
      <li><svg><use href="#arrow-dot"/></svg>Expound the actual teachings of the great explorer of the trutt</li>
      <li><svg><use href="#arrow-dot"/></svg>Master-builder of human happiness.</li>
      <li><svg><use href="#arrow-dot"/></svg>No one rejects, dislikes, or avoids pleasure itself,</li>
      <li><svg><use href="#arrow-dot"/></svg>Those who do not know how to pursue pleasure rational ly encounter extremely painful.</li>
      <li><svg><use href="#arrow-dot"/></svg>Nor again is there anyone who loves</li>
    </ul>
    <ul class="bullets half-b">
      <li><svg><use href="#arrow-dot"/></svg>I must explain to you how all this mistaken idea of denoun cing pleasure and praising pain was born an</li>
      <li><svg><use href="#arrow-dot"/></svg>Expound the actual teachings of the great explorer of the trutt</li>
      <li><svg><use href="#arrow-dot"/></svg>Master-builder of human happiness.</li>
      <li><svg><use href="#arrow-dot"/></svg>No one rejects, dislikes, or avoids pleasure itself,</li>
      <li><svg><use href="#arrow-dot"/></svg>Those who do not know how to pursue pleasure rationally encounter extremely painful.</li>
      <li><svg><use href="#arrow-dot"/></svg>Nor again is there anyone who loves</li>
    </ul>
    <footer class="footer">(C) Copyright 2024 | All Rights Reserved<span class="page-no">Page 03 Of 08</span></footer>
  </section>

  <section class="slide col-a row-4">
    <h2 class="title-band">Why Choose Us</h2>
    <div class="lead">
      <p>I must explain to you how all this mistaken idea of denouncing pleasure and praising pain was born and I will give you a com plete account of the system, and expound the actual teachings of the great explorer of the trutt Master-builder of human happ iness. No one rejects, dislikes, or avoids pleasure itself, because it is pleasure, but because those who do not know how to pursue pleasure rationally encounte</p>
      <p>Nor again is there anyone who loves or pursues or desires to</p>
    </div>
    <div class="illustration" role="img" aria-label="Illustration of a hand placing the next rung on a ladder for a climbing person"></div>
    <footer class="footer">(C) Copyright 2024 | All Rights Reserved<span class="page-no">Page 04 Of 08</span></footer>
  </section>

  <section class="slide col-b row-4">
    <h2 class="title-band">Why Choose Us</h2>
    <article class="feature f1">
      <div class="badge purple">
        <svg viewBox="0 0 24 24" fill="none" stroke="#fff" stroke-width="1.2" stroke-linecap="round"><path d="M8.5 15a5.5 5.5 0 1 1 7 0v2.5h-7z"/><path d="M9.5 19.5h5M10.5 21.5h3"/><circle cx="12" cy="10.5" r="2"/><path d="M12 2v1.5M4 10.5H2.5M21.5 10.5H20M5.5 4.5l1 1M18.5 4.5l-1 1"/></svg>
      </div>
      <h3>Denouncing pleasure</h3>
      <p>Sed ut perspiciatis unde omnis iste natus error sit voluptatem accusantium dolo- remque ntium, totam rem aperiam, eaque ipsa quae ab illo inventore veritatis et quasi architecae vitae dicta suntem aperi- am, eaque ipsa quae</p>
    </article>
    <article class="feature f2">
      <div class="badge blue">
        <svg viewBox="0 0 24 24" fill="none" stroke="#fff" stroke-width="1.2" stroke-linecap="round" stroke-linejoin="round"><circle cx="12" cy="7" r="3"/><path d="M3 14l4-3 4 2 2-1 4 2 4-1M5 17l3 2h4l5-3"/><path d="M12 2v1.5M16.5 7H18M6 7h1.5"/></svg>
      </div>
      <h3>Denouncing pleasure</h3>
      <p>Sed ut perspiciatis unde omnis iste natus error sit voluptatem accusantium dolo- remque ntium, totam rem aperiam, eaque ipsa quae ab illo inventore veritatis et quasi architecae vitae dicta suntem aperi- am, eaque ipsa quae</p>
    </article>
    <article class="feature f3">
      <div class="badge green">
        <svg viewBox="0 0 24 24" fill="none" stroke="#fff" stroke-width="1.2" stroke-linecap="round" stroke-linejoin="round"><path d="M5 21V9h8v12M3 21h18"/><path d="M7.5 12h1M10 12h1M7.5 15h1M10 15h1M8 21v-3h2v3"/><path d="M17 10c-2-2.2-2.5-3.5-2.5-4.5a2.5 2.5 0 0 1 5 0c0 1-.5 2.3-2.5 4.5z"/><circle cx="17" cy="5.5" r=".8"/><path d="M15 21v-7h4v7"/></svg>
      </div>
      <h3>Denouncing pleasure</h3>
      <p>Sed ut perspiciatis unde omnis iste natus error sit voluptatem accusantium dolo- remque ntium, totam rem aperiam, eaque ipsa quae ab illo inventore veritatis et quasi architecae vitae dicta suntem aperi- am, eaque ipsa quae</p>
    </article>
    <footer class="footer">(C) Copyright 2024 | All Rights Reserved<span class="page-no">Page 04 Of 08</span></footer>
  </section>

</main>
</body>
</html>
```